Business Card Design Project

Business Card design based on logo.
Updates

I need business card, letterhead, envelope, and if possible, Powerpoint slide template.

On front of business card: Just logo- and  my name and title:  Harriet Lindqvist, Principal

On reverse-logo and the rest of the contact info:

4871 Quarry Lane
Davis, CA 95618
650-318-2764
hl@brackenstudyworks.example

On letterhead-Just logo at top, at bottom  the rest-very small along the bottom

On PPT slide-just the logo.

I also want to try a few other colors-I like lime/dark grey (not black) but would like to try Sienna, maybe also indigo or bright blue-green.

I forgot to add-

On the business card-switch to vertical on reverse side and put:

Reverse side-switch to vertical and list:

Harriet Lindqvist
Principal
Bracken Study Works, LLC

650-318-2764

4871 Quarry Lane
Davis, CA 95618

Harriet Lindqvist
Principal

650-318-2764

4871 Quarry Lane
Davis, CA 95618

I have another project at the same time-for Stationery. Feel free to submit to that one also.

That one includes letterhead, envelope, PPT slide, folder cover sheet-HL

Industry/Entity Type

Business

Requirements
Must have
• Must use logo-preferably lime green version-with gray, not black or just 2-tone -logo on colored background.

```html
<!DOCTYPE html>
<html lang="en">
<head>
<meta charset="utf-8">
<title>Bracken Study Works – Business Card</title>
<link rel="stylesheet" href="https://fonts.googleapis.com/css2?family=Open+Sans:wght@400;600;700&display=swap">
<style>
  :root {
    --lime: #9cc33b;
    --lime-light: #b5d65a;
    --lime-dark: #86ad2c;
    --grey-dark: #4a4d50;
    --grey-mid: #6f7275;
    --grey-rule: #cfd1d2;
    --paper: #fbfbfa;
    --backdrop: #e9e7e3;
  }
  * { box-sizing: border-box; margin: 0; padding: 0; }
  html, body {
    width: 1200px; height: 900px; overflow: hidden;
    background: var(--backdrop);
    font-family: "Open Sans", Arial, sans-serif;
  }
  .canvas {
    position: relative; width: 1200px; height: 900px;
    display: flex; flex-direction: column; align-items: center; justify-content: center; gap: 52px;
  }
  .card {
    position: relative; width: 620px; height: 354px;
    box-shadow: 0 6px 18px rgba(0,0,0,.14);
  }
  /* Front */
  .card-front { background: var(--paper); }
  .holder { position: absolute; top: 58px; right: 46px; text-align: right; }
  .holder-name { color: var(--lime); font-weight: 700; font-size: 17px; }
  .holder-title { color: var(--grey-mid); font-size: 13px; margin-top: 1px; }
  .top-rule { position: absolute; left: 300px; right: 46px; top: 110px; border-top: 1px solid var(--grey-rule); }
  .wordmark {
    display: flex; align-items: center; gap: 10px;
    color: var(--grey-dark); font-weight: 600; letter-spacing: .18em; text-transform: uppercase;
  }
  .wordmark-square { width: 14px; height: 14px; background: var(--lime); flex: none; }
  .card-front .wordmark { position: absolute; left: 46px; top: 140px; font-size: 19px; }
  .bottom-rule { position: absolute; left: 46px; right: 46px; top: 200px; border-top: 1px solid var(--grey-rule); }
  .address { position: absolute; left: 46px; top: 216px; color: var(--grey-dark); font-size: 13px; line-height: 1.45; }
  .contacts {
    position: absolute; left: 46px; top: 272px;
    display: grid; grid-template-columns: 150px auto; row-gap: 6px; column-gap: 18px;
    color: var(--grey-dark); font-size: 13px;
  }
  .contact { display: flex; align-items: center; gap: 8px; }
  .contact svg { width: 14px; height: 14px; flex: none; fill: var(--lime); }
  .contact-at { color: var(--lime); font-weight: 700; width: 14px; text-align: center; }
  /* Back */
  .card-back {
    background: radial-gradient(ellipse at 40% 45%, var(--lime-light), var(--lime) 60%, var(--lime-dark));
    display: flex; align-items: center; justify-content: center;
  }
  .card-back .wordmark { font-size: 24px; }
  .card-back .wordmark-square { background: var(--paper); width: 18px; height: 18px; }
</style>
</head>
<body>
<main class="canvas">
  <section class="card card-front" aria-label="Business card front">
    <div class="holder">
      <p class="holder-name">Harriet Lindqvist</p>
      <p class="holder-title">Principal</p>
    </div>
    <div class="top-rule"></div>
    <div class="wordmark"><span class="wordmark-square"></span>Bracken Study Works</div>
    <div class="bottom-rule"></div>
    <address class="address" style="font-style:normal">
      4871 Quarry Lane<br>
      Davis, CA 95618, USA
    </address>
    <div class="contacts">
      <div class="contact">
        <svg viewBox="0 0 16 16" aria-hidden="true"><path d="M3.5 1.5l2.5 3-1.5 1.8c.9 2 2.3 3.4 4.2 4.2L10.5 9l3 2.5-1.2 2.6C7 14 2 9 1.9 3.7z"/></svg>
        <span>650.318.2764</span>
      </div>
      <div class="contact">
        <span class="contact-at">@</span>
        <span>hl@brackenstudyworks.example</span>
      </div>
      <div class="contact">
        <svg viewBox="0 0 16 16" aria-hidden="true"><rect x="4" y="1" width="8" height="4"/><rect x="1" y="6" width="14" height="6" rx="1"/><rect x="4" y="10" width="8" height="5" fill="#fff" stroke="#9cc33b" stroke-width="1.2"/></svg>
        <span>650.318.2790</span>
      </div>
      <div class="contact">
        <svg viewBox="0 0 16 16" aria-hidden="true"><path d="M8 1a7 7 0 100 14A7 7 0 008 1zm0 1.5c.8 0 1.8 1.6 2.1 4H5.9c.3-2.4 1.3-4 2.1-4zM2.6 6.5h1.8a13 13 0 000 3H2.6a5.6 5.6 0 010-3zm3.3 3a11 11 0 010-3h4.2a11 11 0 010 3zm5.7 0a13 13 0 000-3h1.8a5.6 5.6 0 010 3zM8 13.5c-.8 0-1.8-1.6-2.1-4h4.2c-.3 2.4-1.3 4-2.1 4z"/></svg>
        <span>www.brackenstudyworks.example</span>
      </div>
    </div>
  </section>

  <section class="card card-back" aria-label="Business card back">
    <div class="wordmark"><span class="wordmark-square"></span>Bracken Study Works</div>
  </section>
</main>
</body>
</html>
```